Real estate broker business card

Want a modern celan but effective business card for my residential and commercial real estate business. I want the back of the card to advertise my services and to capture business. I have attached the back of my current business card fore ideas
Updates

Logos, photo and text updates added! Added Saturday, September 3, 2016

Project Deadline Extended Reason: LOGOS, PHOTOS AND TEST JUST UPLOADED! I'M READY TO PICK A DESIGN! THANK YOU! Added Saturday, September 3, 2016

Target Market(s)

home buyers and seller. commercial buyers and sellers

Industry/Entity Type

Real Estate

Contact Information for Business Card

must have my contact information and my photo

Requirements
Must have
• Carla Ventrino
• Owner & Qualifying Broker
• Ventrino Real Estate Services
• 505.718.2094
• carla@ventrinohomes.example
• www.ventrinohomes.example
Nice to have
• metallic
• Business capture text: " Don't buy or lease property without someone looking out for your best interests. I will represent you on your home or investment purchase for FREE!"
• "Home owners, call today to receive a FREE market analysis for your homes value!

```html
<!DOCTYPE html>
<html lang="en">
<head>
<meta charset="utf-8">
<title>Ventrino Real Estate Services – Business Card</title>
<link rel="stylesheet" href="https://fonts.googleapis.com/css2?family=Arimo:wght@400;700&display=swap">
<style>
  :root {
    --backdrop: #3a3532;
    --card: #141516;
    --card-edge: #0c0c0d;
    --teal: #2e8c98;
    --white: #e9ecee;
    --grey: #8a8d90;
    --deep-grey: #2a2b2d;
    --rule: #6d7073;
  }
  * { box-sizing: border-box; margin: 0; padding: 0; }
  html, body { width: 1200px; height: 864px; overflow: hidden; }
  body {
    background: var(--backdrop);
    font-family: "Arimo", Arial, sans-serif;
    position: relative;
  }
  .card {
    position: absolute;
    width: 525px;
    height: 300px;
    background: var(--card);
    border: 1px solid var(--card-edge);
    box-shadow: 0 14px 30px rgba(0,0,0,.45);
  }
  .card--back { left: 50px; top: 70px; }
  .card--front { left: 625px; top: 440px; }

  /* back */
  .back-mark {
    position: absolute;
    top: 62px; left: 0; right: 0;
    text-align: center;
    display: flex; justify-content: center; align-items: center; gap: 12px;
  }
  .back-mark__dot {
    width: 26px; height: 26px; border-radius: 50%;
    background: var(--deep-grey);
  }
  .back-mark__name {
    font-size: 34px; font-weight: 700; letter-spacing: 4px;
    color: var(--deep-grey);
  }
  .capture {
    position: absolute;
    top: 160px; left: 40px; right: 40px;
    text-align: center;
    font-size: 14px; line-height: 1.45;
    color: var(--grey);
  }

  /* front */
  .brand {
    position: absolute;
    top: 58px; right: 38px;
    display: flex; align-items: center; gap: 14px;
  }
  .brand__badge {
    width: 58px; height: 58px; border-radius: 50%;
    background: var(--teal);
  }
  .brand__name {
    font-size: 20px; font-weight: 700; line-height: 1.15;
    color: var(--teal);
    letter-spacing: 1px;
  }
  .identity {
    position: absolute;
    top: 172px; right: 282px;
    text-align: right;
  }
  .identity__name { font-size: 19px; color: var(--teal); margin-bottom: 3px; }
  .identity__role, .identity__firm { font-size: 15px; color: var(--white); line-height: 1.35; }
  .divider {
    position: absolute;
    left: 260px; top: 165px;
    width: 1px; height: 92px;
    background: var(--rule);
  }
  .contacts {
    position: absolute;
    left: 280px; top: 172px;
    list-style: none;
  }
  .contacts li {
    display: flex; align-items: center; gap: 9px;
    font-size: 14px; color: var(--white);
    line-height: 1.6;
  }
  .contacts svg { width: 13px; height: 13px; fill: var(--teal); flex: none; }
</style>
</head>
<body>

<section class="card card--back" aria-label="Card back">
  <div class="back-mark">
    <span class="back-mark__dot"></span>
    <span class="back-mark__name">VENTRINO</span>
  </div>
  <p class="capture">
    Don't buy or lease property without someone<br>
    looking out for your best interests.<br>
    I will represent you on your home or investment purchase for FREE!
  </p>
</section>

<section class="card card--front" aria-label="Card front">
  <div class="brand">
    <span class="brand__badge"></span>
    <span class="brand__name">VENTRINO<br>REAL ESTATE SERVICES</span>
  </div>

  <div class="identity">
    <p class="identity__name">Carla Ventrino</p>
    <p class="identity__role">Owner &amp; Qualifying Broker</p>
    <p class="identity__firm">Ventrino Real Estate Services</p>
  </div>

  <span class="divider"></span>

  <ul class="contacts">
    <li>
      <svg viewBox="0 0 16 16" aria-hidden="true"><path d="M3.6 1.2l2.3 2.3-1.3 2a9 9 0 005.9 5.9l2-1.3 2.3 2.3-1.6 2.4C7.5 16 0 8.5 1.2 2.8z"/></svg>
      505.718.2094
    </li>
    <li>
      <svg viewBox="0 0 16 16" aria-hidden="true"><path d="M1 3h14v1.2L8 9 1 4.2zM1 5.8l7 4.8 7-4.8V13H1z"/></svg>
      carla@ventrinohomes.example
    </li>
    <li>
      <svg viewBox="0 0 16 16" aria-hidden="true"><circle cx="8" cy="8" r="7"/></svg>
      www.ventrinohomes.example
    </li>
  </ul>
</section>

</body>
</html>
```